Corvel Creamery Works ( Australian Dairy site )

We need a new website we are a new company in Australia manufacturing dairy products ( Packing Butter ) We want to have a new modern punchy website with the basic details of the company and company certifications should be linked in a pdf etc.. maybe photos of the site modernised graphics etc.. we need to show our customers our brand clean and green image of Australian high quality products packed under strict Australian quality standards.

Target Market(s)

export - Asia

Industry/Entity Type

It Company

Number of Pages Required

5+ page

Requirements
Must have
• Home page
• About us page
• Products page
• Contact us page
• Facility / Accreditations ( Under facility pdf files eg Licenses, halal etc.. )

```html
<!DOCTYPE html>
<html lang="en">
<head>
<meta charset="utf-8">
<title>Our Facility – Corvel Creamery Works</title>
<link rel="stylesheet" href="https://fonts.googleapis.com/css2?family=Ubuntu:wght@400;500;700&family=Dancing+Script:wght@700&display=swap">
<style>
:root{
  --sky-top:#d6eafc;
  --sky-mid:#8cc3f5;
  --sky-low:#5ea6ee;
  --green:#3a9e38;
  --green-deep:#2c8a2e;
  --green-dark:#1f6e24;
  --orange:#f5ac1c;
  --white:#ffffff;
  --bark:#5f4a3d;
  --bark-dark:#46362c;
  --muted:#d9cfc6;
  --ink:#333333;
}
*{margin:0;padding:0;box-sizing:border-box}
html,body{width:827px;height:1200px;overflow:hidden}
body{position:relative;font-family:"Ubuntu",sans-serif;background:var(--white);color:var(--ink)}
.abs{position:absolute}
.layer{z-index:2}

/* hero */
.hero{left:0;top:0;width:827px;height:240px;background:radial-gradient(ellipse at 50% -10%,var(--sky-top) 0%,var(--sky-mid) 45%,var(--sky-low) 100%)}
.brand{left:92px;top:20px;display:flex;align-items:center;gap:9px}
.brand-dot{width:72px;height:56px;border-radius:50%;background:var(--green);border:3px solid var(--white)}
.brand-name{font-weight:500;font-size:15px;line-height:16px;color:var(--green-deep)}
.nav{left:347px;top:45px;display:flex;font-size:8px;letter-spacing:.2px}
.nav a{color:var(--white);text-decoration:none;margin-right:26px}
.nav a.current{color:var(--green-dark);font-weight:700}
.hero-title{left:0;width:827px;top:118px;text-align:center;font-family:"Dancing Script",cursive;font-size:50px;color:var(--white);text-shadow:0 2px 3px rgba(0,0,0,.25)}
.hero-sub{left:0;width:827px;top:193px;text-align:center;font-size:7.5px;color:var(--white);font-weight:500}

/* green showcase */
.showcase{left:0;top:200px;width:827px;height:600px;background:linear-gradient(var(--green) 0%,var(--green-deep) 100%)}
.curves{left:0;top:0;width:827px;height:1200px;pointer-events:none}
.show-title{left:0;width:827px;top:286px;text-align:center;font-family:"Dancing Script",cursive;font-size:34px;color:var(--white)}
.slide-frame{left:147px;top:374px;width:533px;height:336px;background:var(--white);padding:6px;box-shadow:0 3px 8px rgba(0,0,0,.3)}
.slide-photo{width:100%;height:100%;background:linear-gradient(180deg,#c9ced2 0%,#a9b0b6 55%,#2a5fb7 78%,#1f4ea3 100%)}
.arrow{width:39px;height:39px;border-radius:50%;background:var(--white);top:523px;display:flex;align-items:center;justify-content:center;box-shadow:0 2px 4px rgba(0,0,0,.25)}

/* thumbnails */
.thumbs{left:85px;top:812px;width:660px;display:flex;justify-content:space-between}
.thumb{width:120px;text-align:center}
.thumb-photo{width:108px;height:74px;margin:0 auto;border:3px solid var(--white);box-shadow:0 1px 4px rgba(0,0,0,.35);background:linear-gradient(180deg,#b6bcc2 0%,#8e969d 60%,#3566b6 100%)}
.thumb-cap{margin-top:17px;font-size:7.6px;line-height:10px;color:var(--green);font-weight:500}

/* footer */
.footer{left:0;top:918px;width:827px;height:282px;background:var(--bark)}
.foot-h{font-size:17px;color:var(--white);font-weight:500;top:1010px}
.foot-list{font-size:7.6px;line-height:13.3px;color:var(--muted);list-style:none}
.contact-row{display:flex;gap:6px;align-items:flex-start;font-size:7.6px;line-height:13.3px;color:var(--muted)}
.news-input{left:390px;top:1070px;width:135px;height:24px;background:var(--bark-dark);color:var(--white);font-size:7.4px;padding:7px 8px}
.subscribe{left:391px;top:1105px;width:58px;height:18px;background:var(--green);color:var(--white);font-size:7.4px;text-align:center;line-height:18px}
.foot-brand{left:552px;top:1018px;display:flex;align-items:center;gap:8px}
.foot-dot{width:78px;height:58px;border-radius:50%;border:3px solid #8d8078;background:#6f5b4e}
.foot-name{font-size:15px;line-height:15px;font-weight:500;color:#a89c93}
.social{top:1081px;width:28px;height:28px;border-radius:50%;background:var(--green);display:flex;align-items:center;justify-content:center}
.copyright{left:0;width:827px;top:1163px;text-align:center;font-size:7.6px;color:var(--white)}
</style>
</head>
<body>

<section class="abs hero" aria-label="Page header"></section>
<section class="abs showcase" aria-label="Facility gallery"></section>

<svg class="abs curves" viewBox="0 0 827 1200" aria-hidden="true">
  <path d="M0,0 H827 V212 Q413,266 0,212 Z" fill="#5ea6ee" opacity="0"/>
  <path d="M0,200 H827 V212 Q413,266 0,212 Z" fill="#5ea6ee"/>
  <path d="M0,212 Q413,266 827,212 L827,222 Q413,292 0,222 Z" fill="#ffffff"/>
  <path d="M0,214 Q413,270 827,214 Q413,286 0,214 Z" fill="#f5ac1c"/>
  <path d="M0,744 Q413,816 827,744 V918 H0 Z" fill="#ffffff"/>
</svg>

<div class="abs brand layer"><span class="brand-dot"></span><span class="brand-name">Corvel<br>Creamery Works</span></div>
<nav class="abs nav layer">
  <a href="#">HOME</a><a href="#">ABOUT US</a><a href="#">PRODUCTS</a><a class="current" href="#">FACILITY</a><a href="#">ACCREDITATIONS</a><a href="#">CONTACT US</a>
</nav>
<h1 class="abs hero-title layer">Our Facility</h1>
<p class="abs hero-sub layer">Corvel Creamery Works has a modern state of the art facility in Victoria Australia.</p>

<h2 class="abs show-title layer">Foreign matter inspection by X-ray machines</h2>
<div class="abs slide-frame layer"><div class="slide-photo" role="img" aria-label="Photo of stainless steel X-ray inspection machine on blue factory floor"></div></div>
<div class="abs arrow layer" style="left:92px" aria-label="Previous slide"><svg width="12" height="14" viewBox="0 0 12 14"><path d="M8,2 L3,7 L8,12" fill="none" stroke="#333" stroke-width="2.6" stroke-linecap="round" stroke-linejoin="round"/></svg></div>
<div class="abs arrow layer" style="left:696px" aria-label="Next slide"><svg width="12" height="14" viewBox="0 0 12 14"><path d="M4,2 L9,7 L4,12" fill="none" stroke="#333" stroke-width="2.6" stroke-linecap="round" stroke-linejoin="round"/></svg></div>

<footer class="abs footer" aria-label="Site footer"></footer>
<svg class="abs curves" viewBox="0 0 827 1200" aria-hidden="true">
  <path d="M0,918 Q413,1042 827,918 V900 H0 Z" fill="#ffffff"/>
  <path d="M112,944 Q413,1008 715,944 Q413,996 112,944 Z" fill="#f5ac1c"/>
</svg>

<div class="abs thumbs layer">
  <div class="thumb"><div class="thumb-photo" role="img" aria-label="Photo of butter wrapping machines"></div><p class="thumb-cap">Kestrel Butter Wrapping<br>machines</p></div>
  <div class="thumb"><div class="thumb-photo" role="img" aria-label="Photo of X-ray inspection machine"></div><p class="thumb-cap">Foreign matter inspection by<br>X-ray machines</p></div>
  <div class="thumb"><div class="thumb-photo" role="img" aria-label="Photo of positive air pressure unit"></div><p class="thumb-cap">Positive Air pressure to<br>maintain an hygienic</p></div>
  <div class="thumb"><div class="thumb-photo" role="img" aria-label="Photo of online check weigher"></div><p class="thumb-cap">Online check weigher</p></div>
  <div class="thumb"><div class="thumb-photo" role="img" aria-label="Photo of automatic case packers"></div><p class="thumb-cap">Automatic case packers</p></div>
</div>

<h3 class="abs foot-h layer" style="left:89px">Quick Links</h3>
<ul class="abs foot-list layer" style="left:89px;top:1040px">
  <li>Home</li><li>About us</li><li>Products</li><li>Facility</li><li>Accreditations</li><li>Contact us</li>
</ul>

<h3 class="abs foot-h layer" style="left:227px">Contact Us</h3>
<div class="abs layer" style="left:227px;top:1043px">
  <div class="contact-row"><svg width="7" height="13" viewBox="0 0 10 10"><path d="M2,1 L4,1 L5,3.5 L3.8,4.5 Q4.8,6.2 6,6.6 L7,5.4 L9,6.5 L9,8.5 Q5,9 2,5 Q1,3 2,1 Z" fill="#d9cfc6"/></svg><span>+61 3 9000 4812</span></div>
  <div class="contact-row"><svg width="8" height="13" viewBox="0 0 10 10"><rect x="1" y="2.5" width="8" height="5.5" fill="none" stroke="#d9cfc6"/><path d="M1,2.5 L5,5.5 L9,2.5" fill="none" stroke="#d9cfc6"/></svg><span>hello@corvelcreamery.example</span></div>
  <div class="contact-row" style="margin-top:13px"><svg width="7" height="13" viewBox="0 0 10 12"><path d="M5,1 Q9,1 9,5 Q9,7 5,11 Q1,7 1,5 Q1,1 5,1 Z" fill="#d9cfc6"/><circle cx="5" cy="4.8" r="1.5" fill="#5f4a3d"/></svg><span>18 Larkin Road, Tullamarine Park,<br>Victoria 3043 Australia</span></div>
</div>

<h3 class="abs foot-h layer" style="left:392px">Newsletter</h3>
<p class="abs layer" style="left:391px;top:1045px;font-size:7.4px;color:var(--muted)">Sign Up for Our Newsletter &amp; Promotion</p>
<div class="abs news-input layer">Enter Your email Id</div>
<div class="abs subscribe layer">SUBSCRIBE</div>

<div class="abs foot-brand layer"><span class="foot-dot"></span><span class="foot-name">Corvel<br>Creamery Works</span></div>
<a class="abs social layer" style="left:644px" href="#" aria-label="Social profile link"><svg width="13" height="13" viewBox="0 0 14 14"><path d="M6,8 L8,6 M5,6.5 L3.5,8 A2.2,2.2 0 0 0 6,10.5 L7.5,9 M9,7.5 L10.5,6 A2.2,2.2 0 0 0 8,3.5 L6.5,5" fill="none" stroke="#fff" stroke-width="1.6" stroke-linecap="round"/></svg></a>
<a class="abs social layer" style="left:675px" href="#" aria-label="Social profile link"><svg width="13" height="13" viewBox="0 0 14 14"><path d="M6,8 L8,6 M5,6.5 L3.5,8 A2.2,2.2 0 0 0 6,10.5 L7.5,9 M9,7.5 L10.5,6 A2.2,2.2 0 0 0 8,3.5 L6.5,5" fill="none" stroke="#fff" stroke-width="1.6" stroke-linecap="round"/></svg></a>
<a class="abs social layer" style="left:708px" href="#" aria-label="Social profile link"><svg width="13" height="13" viewBox="0 0 14 14"><path d="M6,8 L8,6 M5,6.5 L3.5,8 A2.2,2.2 0 0 0 6,10.5 L7.5,9 M9,7.5 L10.5,6 A2.2,2.2 0 0 0 8,3.5 L6.5,5" fill="none" stroke="#fff" stroke-width="1.6" stroke-linecap="round"/></svg></a>

<p class="abs copyright layer">© 2016 corvelcreamery.example</p>

</body>
</html>
```